Stationary design for boutique production house

We need a stationary design for our production house, 'Lorno Productions' based in Singapore. We produce microfilms as well as podcasts, talkshows and events. Our logo is a stylized icon of our director, who is also the executive producer and host of our programs, Lorno. Our main company colors are Red, Black and white. We would like a clean, minimalist design incorporating our existing company logo that conveys a sense of urbanism and elegance.

Logo and font files are attached. f

Target Market(s)

We focus on lifestyle media rather than entertainment.

Industry/Entity Type

Boutique

Font styles to use
Serif
Sans Serif

Colors
ec1f27
ffffff
000000

Requirements
Must have
• Our company logo and at least one of our company colors.
Nice to have
• Our address and contact information.
Should not have
• Changes made to the company logo (using only certain parts of it is fine though)

```html
<!DOCTYPE html>
<html lang="en">
<head>
<meta charset="utf-8">
<title>Lorno Productions – Business Card</title>
<link rel="stylesheet" href="https://fonts.googleapis.com/css2?family=Noto+Serif:wght@400;700&family=Playfair+Display:wght@400&family=Open+Sans:wght@400&display=swap">
<style>
  :root {
    --red: #ec1f27;
    --black: #000000;
    --ink: #231f20;
    --card-dark: #231f20;
    --paper: #f7f7f7;
    --white: #ffffff;
    --text: #3a3a3a;
    --stage: #555555;
    --faint: #2c2829;
  }
  * { margin: 0; padding: 0; box-sizing: border-box; }
  html, body { width: 1200px; height: 750px; overflow: hidden; }
  body { background: var(--stage); position: relative; font-family: "Noto Serif", serif; }

  .card { position: absolute; top: 228px; width: 462px; height: 263px; overflow: hidden; }
  .card-front { left: 124px; background: var(--paper); }
  .card-back { left: 595px; background: var(--card-dark); }

  /* front */
  .edge-dot { position: absolute; left: -27px; top: 28px; width: 36px; height: 36px; border-radius: 50%; background: var(--red); }
  .person-name { position: absolute; left: 26px; top: 35px; font-weight: 700; font-size: 16.5px; line-height: 20px; color: var(--red); letter-spacing: 0.2px; white-space: nowrap; }
  .person-role { position: absolute; left: 25px; top: 63px; font-size: 12.5px; line-height: 16px; color: var(--ink); white-space: nowrap; }
  .address { position: absolute; left: 27px; top: 94px; font-size: 11px; line-height: 16px; color: var(--text); white-space: nowrap; }
  .contacts { position: absolute; left: 27px; top: 137px; list-style: none; }
  .contacts li { display: flex; align-items: center; height: 18.5px; font-size: 11px; color: var(--text); white-space: nowrap; }
  .contacts svg { width: 12px; height: 12px; margin-right: 8px; fill: var(--red); flex: none; }

  .brand-front { position: absolute; left: 304px; top: 140px; width: 140px; text-align: center; }
  .brand-front .brand-dot { display: block; width: 10px; height: 10px; border-radius: 50%; background: var(--red); margin: 0 auto 14px; }
  .brand-front .brand-name { font-family: "Playfair Display", serif; font-size: 15px; line-height: 18px; color: var(--ink); white-space: nowrap; }

  .bottom-band { position: absolute; left: 0; bottom: 0; width: 100%; height: 17px; }

  /* back */
  .brand-back { position: absolute; left: 0; top: 160px; width: 208px; text-align: center; }
  .brand-back .brand-name { font-family: "Playfair Display", serif; font-size: 21px; line-height: 25px; color: var(--white); white-space: nowrap; }
  .brand-back .web { margin-top: 16px; font-family: "Open Sans", sans-serif; font-size: 10.5px; letter-spacing: 2.6px; color: var(--white); white-space: nowrap; }
  .back-circle { position: absolute; left: 256px; top: 20px; width: 220px; height: 220px; border-radius: 50%; background: var(--faint); }
</style>
</head>
<body>

<section class="card card-front">
  <span class="edge-dot"></span>
  <h1 class="person-name">DANIEL REYES</h1>
  <p class="person-role">CEO/Founder</p>
  <p class="address">14 Tanjong Pagar Road<br>Singapore 088452</p>
  <ul class="contacts">
    <li><svg viewBox="0 0 12 12"><path d="M2.4 0.6 4.3 2.8 3.3 4.2C4 5.8 5.4 7.3 7.6 8.6L9 7.6 11.4 9.6 10.4 11.4C6 11.2 0.9 6.2 0.6 1.6Z"/></svg>612 905 3371</li>
    <li><svg viewBox="0 0 12 12"><path d="M3 0h6a1 1 0 0 1 1 1v10a1 1 0 0 1-1 1H3a1 1 0 0 1-1-1V1a1 1 0 0 1 1-1Zm.4 1.6v7.4h5.2V1.6Z"/></svg>834 217 6620</li>
    <li><svg viewBox="0 0 12 12"><path d="M3 0h6v3H3Zm-2 4h10a1 1 0 0 1 1 1v4h-2v3H2V9H0V5a1 1 0 0 1 1-1Zm2 4v3h6V8Z"/></svg>485 730 1192</li>
    <li><svg viewBox="0 0 12 12"><path d="M0 2h12v8H0Zm1.2 1.2v.5L6 7l4.8-3.3v-.5L6 6.3Z"/></svg>hello@lornostudio.com</li>
    <li><svg viewBox="0 0 12 12"><circle cx="6" cy="6" r="5.5"/><path d="M3 3.5c1 .2 1.6 1 1.3 2 .6.6 1.8.4 1.8 1.6 0 .8-.6 1.2-.3 2.4M7.5 1.2c0 1 .6 1.6 1.6 1.6M9.4 6.4c-.7 0-1.3.5-1.3 1.3" stroke="#fff" stroke-width=".9" fill="none"/></svg>www.lornostudio.com</li>
  </ul>

  <div class="brand-front">
    <span class="brand-dot"></span>
    <p class="brand-name">LORNO<br>PRODUCTIONS</p>
  </div>

  <svg class="bottom-band" viewBox="0 0 462 17" preserveAspectRatio="none">
    <rect width="462" height="17" fill="var(--ink)"/>
    <polygon points="297,17 301,0 303,0 299,17" fill="var(--white)"/>
    <polygon points="303,0 462,0 462,17 299,17" fill="var(--red)"/>
  </svg>
</section>

<section class="card card-back">
  <span class="back-circle"></span>
  <div class="brand-back">
    <p class="brand-name">LORNO<br>PRODUCTIONS</p>
    <p class="web">www.lornostudio.com</p>
  </div>
</section>

</body>
</html>
```